Fresh Dwelling Tract Guide needs a new Landing Page

I like to get a landing page or website with 2-3 pages to help target home buyers who are looking to buy homes from builders such as TW Residences, Morvik, P.L. Fennick, etc. The landing page/website to be non-cluttered and be able to explain to home buyers that there are many benefits to include me as their buyer's agent when they buy a brand new home from any builders.
I may want to incorporate a short explanation video (animated) on the landing page and then for the viewer to click on a button that will take them to another page where they can search for new homes from different builders.
Target Market(s)
Home buyers looking to buy brand new home from builders such as TW Residences, Morvik, P.L. Fennick, etc.
Industry/Entity Type
Real Estate
Number of Pages Required
2 page
Font styles to use
Requirements
Must have
- The landing page may have the explanation video at the bottom of the landing page (scrolled down) or there may be a CALL TO ACTION button that takes the viewer to the 2nd page to watch the explanation video. Once they watched the explanation video and are still interested, they can click on another CALL TO ACTION button that will take them to another website that they will be able to search for all the available new homes and register their contact information.
Should not have
- No clutters and no dark colors.

```html
<!DOCTYPE html>
<html lang="en">
<head>
<meta charset="utf-8">
<title>Fresh Dwelling Tract Guide</title>
<link rel="stylesheet" href="https://fonts.googleapis.com/css2?family=Montserrat:wght@700;800&family=Open+Sans:wght@400;600&display=swap">
<style>
  :root {
    --accent: #f4572c;
    --ink: #111111;
    --text-muted: #666666;
    --white: #ffffff;
    --sky-top: #5b6a86;
    --sky-glow: #e8a25a;
    --lawn: #3c4a22;
  }
  * { box-sizing: border-box; margin: 0; padding: 0; }
  html, body { width: 1200px; height: 1002px; overflow: hidden; background: var(--white); }
  .page { position: relative; width: 1200px; height: 1002px; font-family: "Open Sans", sans-serif; }

  .hero-art { position: absolute; left: 0; top: 0; width: 1200px; height: 745px; }

  .menu-toggle {
    position: absolute; left: 1047px; top: 37px; width: 52px; height: 52px;
    border-radius: 50%; background: #1a1a1a; border: 5px solid rgba(120,120,120,.6);
    display: flex; align-items: center; justify-content: center;
  }

  .hero-title {
    position: absolute; left: 0; top: 290px; width: 1200px; text-align: center;
    font-family: "Montserrat", sans-serif; font-weight: 800; font-size: 50px;
    color: var(--white); letter-spacing: 0.5px; text-transform: uppercase;
    text-shadow: 0 2px 6px rgba(0,0,0,.35);
  }
  .hero-subtitle {
    position: absolute; left: 0; top: 375px; width: 1200px; text-align: center;
    font-size: 27px; color: var(--white); text-shadow: 0 2px 4px rgba(0,0,0,.4);
  }
  .cta-button {
    position: absolute; left: 449px; top: 446px; width: 303px; height: 66px;
    border-radius: 33px; background: var(--accent); color: var(--white);
    font-family: "Montserrat", sans-serif; font-weight: 700; font-size: 18px;
    display: flex; align-items: center; justify-content: center; text-decoration: none;
  }
  .play-button { position: absolute; left: 571px; top: 562px; width: 58px; height: 58px; }

  .social-list { position: absolute; left: 0; top: 776px; width: 1200px; display: flex; justify-content: center; gap: 8px; list-style: none; }
  .social-list li {
    width: 50px; height: 50px; border-radius: 50%; border: 1px solid #8a8a8a;
    display: flex; align-items: center; justify-content: center;
  }
  .social-list li span { width: 12px; height: 12px; border-radius: 50%; background: var(--accent); }

  .contact-line, .footer-links, .copyright {
    position: absolute; left: 0; width: 1200px; text-align: center;
    color: var(--text-muted); font-size: 15px;
  }
  .contact-line { top: 864px; display: flex; justify-content: center; align-items: center; gap: 9px; }
  .contact-line svg { vertical-align: middle; }
  .contact-item { display: inline-flex; align-items: center; gap: 8px; }
  .footer-links { top: 903px; }
  .footer-links a { color: var(--text-muted); text-decoration: none; }
  .sep { margin: 0 14px; }
  .copyright { top: 940px; }
</style>
</head>
<body>
<main class="page">
  <svg class="hero-art" viewBox="0 0 1200 745" xmlns="http://www.w3.org/2000/svg">
    <defs>
      <linearGradient id="heroPhoto" x1="0" y1="0" x2="0" y2="1">
        <stop offset="0" stop-color="#5b6a86"/>
        <stop offset="0.28" stop-color="#b98a6a"/>
        <stop offset="0.42" stop-color="#e8a25a"/>
        <stop offset="0.6" stop-color="#6b5a44"/>
        <stop offset="1" stop-color="#3c4a22"/>
      </linearGradient>
    </defs>
    <polygon points="0,551 816,741 1200,553 1200,557 814,718 0,551" fill="#f4572c"/>
    <polygon role="img" aria-label="Photo of a two-storey family home with a white picket fence and lawn at sunset" points="0,0 1200,0 1200,557 814,718 0,551" fill="url(#heroPhoto)"/>
  </svg>

  <div class="menu-toggle" aria-label="Menu">
    <svg width="20" height="16" viewBox="0 0 20 16"><rect y="0" width="20" height="3" rx="1.5" fill="#fff"/><rect y="6.5" width="20" height="3" rx="1.5" fill="#fff"/><rect y="13" width="20" height="3" rx="1.5" fill="#fff"/></svg>
  </div>

  <h1 class="hero-title">Fresh Dwelling Tract Guide</h1>
  <p class="hero-subtitle">Nam libero tem soluta nobis est eligendi optio cumq</p>
  <a class="cta-button" href="#">FIND YOUR DREAM HOME</a>

  <svg class="play-button" viewBox="0 0 58 58" aria-label="Play video">
    <circle cx="29" cy="29" r="29" fill="#111"/>
    <polygon points="22,16 43,29 22,42" fill="#fff"/>
  </svg>

  <ul class="social-list" aria-label="Social links">
    <li><span></span></li>
    <li><span></span></li>
    <li><span></span></li>
    <li><span></span></li>
  </ul>

  <p class="contact-line">
    <span class="contact-item">
      <svg width="11" height="16" viewBox="0 0 11 16"><path d="M5.5 0A5.5 5.5 0 0 0 0 5.5C0 10 5.5 16 5.5 16S11 10 11 5.5A5.5 5.5 0 0 0 5.5 0zm0 8a2.5 2.5 0 1 1 0-5 2.5 2.5 0 0 1 0 5z" fill="#f4572c"/></svg>
      418 Maple Crest Lane, MO 63010
    </span>
    <span>|</span>
    <span class="contact-item">
      <svg width="14" height="14" viewBox="0 0 14 14"><path d="M3 0l2.5 3.2-1.4 1.8c.9 1.9 2.5 3.6 4.6 4.6l1.8-1.4L14 10.6 12.2 13.5C6 13.8.2 8 .5 1.8z" fill="#f4572c"/></svg>
      1 555 010 0199
    </span>
    <span>|</span>
    <span class="contact-item">
      <svg width="17" height="13" viewBox="0 0 17 13"><rect width="17" height="13" rx="1.5" fill="#f4572c"/><path d="M1 1.5l7.5 5.5L16 1.5" stroke="#fff" stroke-width="1.6" fill="none"/></svg>
      hello@freshdwellingtractguide.com
    </span>
  </p>

  <nav class="footer-links">
    <a href="#">Help</a><span class="sep">|</span><a href="#">FAQ</a><span class="sep">|</span><a href="#">Support</a><span class="sep">|</span><a href="#">Sitemap</a><span class="sep">|</span><a href="#">Terms Of Use</a><span class="sep">|</span><a href="#">Privacy Statement</a>
  </nav>

  <p class="copyright">Fresh Dwelling Tract Guide © 2018 All rights reserved.</p>
</main>
</body>
</html>
```